Moravel Aesthetic Doctor

I require an elegant, luxurious looking business card for my aesthetic business. I am a doctor and that will set me aside from competitors. I am planning to provide home and spa based treatments to clients with high expectations. I have attached my logo.

```html
<!DOCTYPE html>
<html lang="en">
<head>
<meta charset="utf-8">
<title>Moravel Aesthetic Doctor – Business Card</title>
<link href="https://fonts.googleapis.com/css2?family=Arimo:wght@400;700&display=swap" rel="stylesheet">
<style>
  :root {
    --page-bg: #e9ebee;
    --card-white: #ffffff;
    --blue-deep: #0f76cc;
    --blue-mid: #2a90da;
    --blue-light: #4fb3e6;
    --accent-blue: #43aee3;
    --text-grey: #8f9296;
    --name-grey: #9a9da1;
    --rule-grey: #c9cbcd;
    --shadow: rgba(20, 30, 45, 0.18);
  }
  * { box-sizing: border-box; margin: 0; padding: 0; }
  html, body {
    width: 1200px; height: 1015px; overflow: hidden;
    background: var(--page-bg);
    font-family: "Arimo", Arial, sans-serif;
  }
  .canvas {
    width: 1200px; height: 1015px;
    display: flex; flex-direction: column; align-items: center; justify-content: center;
    gap: 34px;
  }
  .card {
    width: 800px; height: 457px;
    box-shadow: 0 10px 30px var(--shadow);
    position: relative; overflow: hidden;
  }

  /* Back side: services */
  .card--services {
    background: linear-gradient(160deg, var(--blue-light) 0%, var(--blue-deep) 45%, var(--blue-mid) 75%, var(--blue-light) 100%);
    display: flex; align-items: center; justify-content: center;
  }
  .services-list {
    list-style: none; text-align: center;
    color: #ffffff; font-size: 22px; letter-spacing: 0.5px; line-height: 1.45;
  }

  /* Front side: contact */
  .card--contact {
    background: var(--card-white);
    display: flex; align-items: center;
  }
  .brand {
    width: 360px; padding-left: 70px;
    display: flex; align-items: center; gap: 18px;
  }
  .brand-mark {
    width: 60px; height: 60px; border-radius: 50%;
    border: 2px solid var(--rule-grey); flex: none;
  }
  .brand-name {
    font-size: 25px; font-weight: 400; color: var(--text-grey);
    line-height: 1.25; letter-spacing: 1px; text-transform: uppercase;
  }
  .divider {
    width: 1px; height: 210px; background: var(--rule-grey); margin: 0 34px 0 10px;
  }
  .details { color: var(--text-grey); }
  .person-name {
    font-size: 27px; font-weight: 700; color: var(--name-grey);
  }
  .person-name .post-nominals {
    font-size: 15px; font-weight: 400; color: var(--accent-blue); letter-spacing: 0.5px;
  }
  .qualification {
    font-size: 19px; color: var(--accent-blue); line-height: 1.25; margin: 6px 0 18px;
  }
  .contact-line {
    display: flex; align-items: center; gap: 10px;
    font-size: 18px; margin-bottom: 6px;
  }
  .contact-line svg { width: 18px; height: 18px; flex: none; }
  .web-row { display: flex; align-items: center; gap: 7px; margin-top: 14px; }
  .social-dot {
    width: 26px; height: 26px; border-radius: 50%;
    border: 1.5px solid var(--accent-blue);
  }
  .web-address { font-size: 18px; margin-left: 8px; }
</style>
</head>
<body>
<main class="canvas">
  <section class="card card--services" aria-label="Card back: treatments">
    <ul class="services-list">
      <li>DERMAL INJECTABLES</li>
      <li>PLASMA FACIALS</li>
      <li>MICRONEEDLING</li>
      <li>SKIN BOOSTERS</li>
      <li>EXCESSIVE SWEATING</li>
      <li>HOME AND SPA BASED TREATMENTS</li>
    </ul>
  </section>

  <section class="card card--contact" aria-label="Card front: contact">
    <div class="brand">
      <span class="brand-mark" aria-hidden="true"></span>
      <p class="brand-name">Moravel<br>Aesthetic Doctor</p>
    </div>
    <span class="divider" aria-hidden="true"></span>
    <div class="details">
      <h1 class="person-name">Dr Elena Varsk <span class="post-nominals">MRCPCH MD</span></h1>
      <p class="qualification">Australasian Diploma of<br>Aesthetic Medicine</p>
      <p class="contact-line">
        <svg viewBox="0 0 24 24" aria-hidden="true"><path fill="#43aee3" d="M6.6 10.8a15.1 15.1 0 0 0 6.6 6.6l2.2-2.2a1 1 0 0 1 1-.25 11.4 11.4 0 0 0 3.6.57 1 1 0 0 1 1 1V20a1 1 0 0 1-1 1A17 17 0 0 1 3 4a1 1 0 0 1 1-1h3.5a1 1 0 0 1 1 1c0 1.25.2 2.45.57 3.57a1 1 0 0 1-.25 1z"/></svg>
        0800 555 017
      </p>
      <p class="contact-line">
        <svg viewBox="0 0 24 24" aria-hidden="true"><path fill="#43aee3" d="M2 5h20v14H2zm2 2v.5l8 5 8-5V7zm0 2.8V17h16V9.8l-8 5z"/></svg>
        elena@moravel.co.nz
      </p>
      <div class="web-row">
        <span class="social-dot" aria-hidden="true"></span>
        <span class="social-dot" aria-hidden="true"></span>
        <span class="social-dot" aria-hidden="true"></span>
        <span class="web-address">www.moravel.co.nz</span>
      </div>
    </div>
  </section>
</main>
</body>
</html>
```